Vorn upkeep KT Solar Venture

Solar power system install
Services and maintenance
wiring, Rewinding and Renovation
Switch Board Upgrade
Power and lighting point
t doesn’t matter how much you spend on quality parts, your solar system will let you down if your design and installation are sub-par. Have your solar system tailored and installed by our Master Electrician and Bright Grid Guild Accredited team.

Target Market(s)

sales and installed

Industry/Entity Type

Solar install and retailer

Contact Information for Business Card

Name , Email, Phone Number ,Business address,

Font styles to use
Serif

Colors
0054AA
0677BA
7BADD7
CADEEF
E8F1F8

Requirements
Must have
• clear and bright
Nice to have
• new design
Should not have
• unclear pictures

```html
<!DOCTYPE html>
<html lang="en">
<head>
<meta charset="utf-8">
<title>Vorn upkeep – KT Solar Venture business card</title>
<link rel="stylesheet" href="https://fonts.googleapis.com/css2?family=Roboto:wght@400;500;700;900&display=swap">
<style>
  :root {
    --page: #e9ecef;
    --blue-deep: #0054aa;
    --blue-mid: #0677ba;
    --teal: #1a8f9a;
    --green: #6bb83a;
    --green-dark: #2e8b2e;
    --green-line: #62b23a;
    --band: #e6e7e8;
    --ink: #1d1d1d;
    --paper: #f3f3f3;
    --muted-sun: #f2a81d;
  }
  * { margin: 0; padding: 0; box-sizing: border-box; }
  html, body { width: 1200px; height: 1138px; overflow: hidden; }
  body {
    background: var(--page);
    font-family: "Roboto", sans-serif;
    position: relative;
    color: var(--ink);
  }
  .card {
    position: absolute;
    width: 620px;
    height: 375px;
    border-radius: 16px;
    overflow: hidden;
    box-shadow: 0 6px 14px rgba(0,0,0,.25);
  }
  /* front */
  .card-front {
    left: 274px; top: 186px;
    background: linear-gradient(115deg, var(--blue-mid) 0%, var(--teal) 45%, var(--green) 100%);
  }
  .brand {
    position: absolute;
    display: flex;
    align-items: center;
    gap: 14px;
  }
  .brand-dot {
    width: 74px; height: 74px;
    border-radius: 50%;
    background: var(--muted-sun);
  }
  .brand-name {
    font-weight: 900;
    line-height: 1.05;
    letter-spacing: .5px;
    text-transform: uppercase;
  }
  .card-front .brand { left: 106px; top: 100px; }
  .card-front .brand-name { color: #ffffff; font-size: 31px; }
  .services-band {
    position: absolute;
    left: 0; top: 239px;
    width: 100%; height: 74px;
    background: var(--band);
    display: flex; flex-direction: column;
    justify-content: center; align-items: center;
    gap: 5px;
    font-size: 15.5px;
    color: var(--ink);
  }
  .web-line {
    position: absolute;
    left: 0; top: 332px; width: 100%;
    display: flex; justify-content: center; align-items: center;
    gap: 24px;
    color: #ffffff;
    font-size: 15px;
  }
  .web-line .rule { width: 80px; height: 2px; background: rgba(255,255,255,.75); }

  /* back */
  .card-back { left: 276px; top: 608px; background: var(--paper); }
  .card-back .brand { left: 20px; top: 48px; }
  .card-back .brand-name { color: var(--blue-deep); font-size: 31px; }
  .person { position: absolute; left: 34px; top: 200px; }
  .person-name { font-size: 25px; font-weight: 700; color: var(--blue-deep); }
  .person-role { font-size: 16px; margin-top: 4px; }
  .divider { position: absolute; left: 28px; top: 236px; }
  .windfarm {
    position: absolute; left: 476px; top: 200px;
    width: 120px; height: 50px;
    background: linear-gradient(90deg, rgba(98,178,58,.25), rgba(98,178,58,.55));
    border-radius: 4px;
  }
  .contacts {
    position: absolute; left: 34px; top: 282px;
    list-style: none; font-size: 16.5px;
  }
  .contacts li { display: flex; align-items: center; gap: 14px; height: 24px; }
  .contacts svg { width: 16px; height: 16px; }
  .address {
    position: absolute; right: 34px; top: 306px;
    text-align: right; font-size: 16.5px; line-height: 24px;
  }
</style>
</head>
<body>

<section class="card card-front">
  <div class="brand">
    <span class="brand-dot"></span>
    <p class="brand-name">Vorn upkeep<br>KT Solar Venture</p>
  </div>
  <div class="services-band">
    <p>Solar Power System Install &nbsp;|&nbsp; Wiring, Rewinding &amp; Renovation</p>
    <p>Services &amp; Maintenance &nbsp;|&nbsp; Switch Board Upgrade &nbsp;|&nbsp; Power &amp; Lighting Point</p>
  </div>
  <div class="web-line">
    <span class="rule"></span>
    <span>www.ktsolarventure.com</span>
    <span class="rule"></span>
  </div>
</section>

<section class="card card-back">
  <div class="brand">
    <span class="brand-dot"></span>
    <p class="brand-name">Vorn upkeep<br>KT Solar Venture</p>
  </div>

  <div class="person">
    <p class="person-name">Mara Lenn Holt</p>
    <p class="person-role">Managing Director</p>
  </div>

  <svg class="divider" width="580" height="30" viewBox="0 0 580 30" aria-hidden="true">
    <path d="M0 26 H200 C230 26 230 12 260 12 H570" fill="none" stroke="var(--green-line)" stroke-width="2"/>
  </svg>
  <div class="windfarm" role="img" aria-label="Small wind turbines and a leaf along the divider line"></div>

  <ul class="contacts">
    <li>
      <svg viewBox="0 0 16 16" aria-hidden="true"><path d="M3 2h3l1 3-2 1c1 2 2 3 4 4l1-2 3 1v3c0 1-1 2-2 2C6 14 2 10 2 4c0-1 0-2 1-2z" fill="var(--green-dark)"/></svg>
      <span>828-555-0142</span>
    </li>
    <li>
      <svg viewBox="0 0 16 16" aria-hidden="true"><rect x="1" y="3" width="14" height="10" fill="var(--green-dark)"/><path d="M1 3l7 6 7-6M1 13l5-5M15 13l-5-5" stroke="#fff" stroke-width="1.2" fill="none"/></svg>
      <span>mara@ktsolarventure.com</span>
    </li>
    <li>
      <svg viewBox="0 0 16 16" aria-hidden="true"><circle cx="8" cy="8" r="6.5" fill="none" stroke="var(--green-dark)" stroke-width="1.5"/><path d="M1.5 8h13M8 1.5c-3 3-3 10 0 13M8 1.5c3 3 3 10 0 13" fill="none" stroke="var(--green-dark)" stroke-width="1.2"/></svg>
      <span>www.ktsolarventure.com</span>
    </li>
  </ul>

  <p class="address">58 Ridgeway Rd., Elm Vale,<br>Brookford, US 204817</p>
</section>

</body>
</html>
```